Online Games Mobile Website Design

Important information:<br/>Style:<br/>- minimalistic flat<br/>- attention to the elements<br/>- The background is everywhere white, except for header, menu and footer.<br/>- everything is flat, without shadows, roundings, bulges, gradients<br/>- free choice of colors<br/>- use bright colors for contrasts<br/>- for a specific page, it is important to save every pixel in height (no need to make pointlessly large indents where they are not needed)<br/><br/>Fonts (recommended, but not required):<br/>for titles (red in layout) - Google sans<br/>for the rest of the text - Roboto<br/><br/>Features:<br/>All pictures of games (pictures with previews of games) should be with an aspect ratio of 16: 9, no others, this should immediately be taken into account.<br/><br/>Additionally, you need to make a logo redesign that will suit the new design.<br/><br/><br/>Specifically about the page to be redesigned - Page of the game<br/>This page contains the game and a list of similar games.<br/><br/>Check attached image for the layout details.<br/><br/>The description of the game is shown by clicking on the name of the game under the game.<br/>For evaluation, you need to provide a page with an open / hidden description of the game.<br/>When the description of the game is disclosed, there are Tag 1, Tag 2, Tag 3 labels - these are the tags to which the game belongs (shooter, arcade, racing, etc.).<br/>You need to choose a set of icons for tags, then use them on these labels.<br/><br/>Under the game (portrait) is a list of similar games.<br/>You must provide 3 options for this list:<br/><br/>1. List items have a border and are separated by indentation.<br/>2. List items without a border are separated by a horizontal line.<br/>3. Items without a border are only separated by indentation<br/>for point 2 and 3, center the text (to the right of the game image) along the upper left edge, as in a relayed video on youtube<br/><br/>For the design layout use pictures, texts, game names from the website Vultaroo.com.

Hello, I've posted my project just today. Thanks in advance

Target Market(s)

Mobile online games

Logo Text

Vultaroo / Online games

Number of Pages Required

1 page

Font styles to use
Sans Serif

Colors

Designer to choose colors to be used in the design.

Requirements
Must have
• Check our current Game Page view and do something that really much much better - https://vultaroo.com/winter-otter-dash-177/

```html
<!DOCTYPE html>
<html lang="en">
<head>
<meta charset="utf-8">
<title>Vultaroo – Winter Otter Dash</title>
<link href="https://fonts.googleapis.com/css2?family=Open+Sans:wght@600;700;800&family=Roboto:wght@400;500;700&display=swap" rel="stylesheet">
<style>
:root{
  --backdrop:#eef0f2;
  --white:#ffffff;
  --red:#e5252f;
  --teal:#1fb5d6;
  --ink:#1d1d1f;
  --muted:#6b6f75;
  --line:#dcdfe3;
  --arrow:#7cc242;
}
*{box-sizing:border-box;margin:0;padding:0}
html,body{width:742px;height:1200px;overflow:hidden;background:var(--backdrop)}
body{font-family:"Roboto",Arial,sans-serif;color:var(--ink)}
.page{position:absolute;left:161px;top:15px;width:420px;height:1170px;background:var(--white);display:flex;flex-direction:column}
.site-header{height:52px;display:flex;align-items:center;justify-content:space-between;padding:0 16px;background:var(--white)}
.brand{display:flex;align-items:center;gap:8px}
.brand-dot{width:22px;height:22px;border-radius:50%;background:var(--red)}
.brand-text{display:flex;flex-direction:column;line-height:1}
.brand-name{font-family:"Open Sans",Arial,sans-serif;font-weight:700;font-size:18px;color:var(--red)}
.brand-tag{font-family:"Open Sans",Arial,sans-serif;font-weight:700;font-size:11px;color:var(--red);margin-top:2px}
.menu-icon{width:22px;height:16px}
.hero{position:relative;height:160px;background:linear-gradient(180deg,#5aa7cf 0%,#8fc8de 55%,#e9f3f6 100%);display:flex;flex-direction:column;align-items:center;justify-content:center;gap:12px}
.hero-title{font-family:"Open Sans",Arial,sans-serif;font-weight:800;font-size:40px;color:var(--white);letter-spacing:1px}
.btn-play{background:var(--red);color:var(--white);font-family:"Open Sans",Arial,sans-serif;font-weight:700;font-size:13px;padding:8px 16px}
.game-head{height:38px;display:flex;align-items:center;justify-content:space-between;padding:0 14px;font-family:"Open Sans",Arial,sans-serif;font-weight:700;font-size:12px}
.game-plays{color:var(--red)}
.game-preview{position:relative;height:170px}
.preview-a{background:linear-gradient(135deg,#4bb3e8 0%,#e23b3b 45%,#8cd23b 75%,#f5d31e 100%)}
.preview-b{background:linear-gradient(160deg,#bfe3f3 0%,#e6f4fa 50%,#9fd3ea 100%)}
.next{position:absolute;right:12px;top:50%;margin-top:-16px;width:32px;height:32px}
.similar{padding:12px 14px 0;display:flex;flex-direction:column;gap:12px}
.card{height:104px;border:1px solid var(--line);display:flex;gap:12px;padding:10px}
.thumb{width:110px;height:62px;flex:none}
.t-orange{background:linear-gradient(135deg,#f6a623,#e64b2a)}
.t-blue{background:linear-gradient(135deg,#2d8fd8,#f3c21d)}
.t-green{background:linear-gradient(135deg,#7dc242,#3a7d2a)}
.t-field{background:linear-gradient(135deg,#9ad06b,#d9b35a)}
.card-body{display:flex;flex-direction:column;gap:5px}
.card-title{font-family:"Open Sans",Arial,sans-serif;font-weight:700;font-size:13px;color:var(--red);text-transform:uppercase}
.card-text{font-size:10.5px;line-height:1.35;color:var(--muted)}
.card-plays{font-size:9px;color:var(--teal);font-weight:500}
.bottom-menu{height:48px;margin-top:auto;display:flex;align-items:center;justify-content:center}
.site-footer{height:30px;background:var(--red);color:var(--white);display:flex;align-items:center;justify-content:space-between;padding:0 14px;font-size:9px}
</style>
</head>
<body>
<div class="page">
  <header class="site-header">
    <div class="brand">
      <span class="brand-dot"></span>
      <div class="brand-text">
        <span class="brand-name">Vultaroo</span>
        <span class="brand-tag">Online Games</span>
      </div>
    </div>
    <svg class="menu-icon" viewBox="0 0 22 16"><rect width="22" height="3" fill="#1fb5d6"/><rect y="6.5" width="22" height="3" fill="#1fb5d6"/><rect y="13" width="22" height="3" fill="#1fb5d6"/></svg>
  </header>

  <section class="hero" role="img" aria-label="Snowy winter scene with game characters and gifts">
    <div class="hero-title">VULTAROO</div>
    <div class="btn-play">PLAY NOW</div>
  </section>

  <div class="game-head"><span>WINTER OTTER DASH</span><span class="game-plays">163,487,211 PLAYS</span></div>
  <div class="game-preview preview-a" role="img" aria-label="Game preview: cheerful fruit characters in winter hats">
    <svg class="next" viewBox="0 0 32 32"><circle cx="16" cy="16" r="16" fill="#7cc242"/><path d="M13 9l7 7-7 7" stroke="#fff" stroke-width="3" fill="none"/></svg>
  </div>

  <div class="similar">
    <article class="card">
      <div class="thumb t-orange" role="img" aria-label="Game preview: snake in an orchard"></div>
      <div class="card-body">
        <h3 class="card-title">Berry Serpent</h3>
        <p class="card-text">Guide the hungry snake through the orchard and gobble up every ripe fruit.</p>
        <span class="card-plays">8K PLAYS</span>
      </div>
    </article>
    <article class="card">
      <div class="thumb t-blue" role="img" aria-label="Game preview: rider on a dirt bike"></div>
      <div class="card-body">
        <h3 class="card-title">Dirt Rally</h3>
        <p class="card-text">Jump your bike over dunes, ramps and hills to reach the finish first.</p>
        <span class="card-plays">8K PLAYS</span>
      </div>
    </article>
  </div>

  <div class="game-head"><span>WINTER OTTER DASH</span><span class="game-plays">163,487,211 PLAYS</span></div>
  <div class="game-preview preview-b" role="img" aria-label="Game preview: character sledding down a snowy slope">
    <svg class="next" viewBox="0 0 32 32"><circle cx="16" cy="16" r="16" fill="#7cc242"/><path d="M13 9l7 7-7 7" stroke="#fff" stroke-width="3" fill="none"/></svg>
  </div>

  <div class="similar">
    <article class="card">
      <div class="thumb t-green" role="img" aria-label="Game preview: monster truck on rough ground"></div>
      <div class="card-body">
        <h3 class="card-title">Giant Wheels</h3>
        <p class="card-text">Drive a huge truck over crushed cars and rough dirt in this wild race.</p>
        <span class="card-plays">8K PLAYS</span>
      </div>
    </article>
    <article class="card">
      <div class="thumb t-field" role="img" aria-label="Game preview: tractor on a farm"></div>
      <div class="card-body">
        <h3 class="card-title">Farm Hauler</h3>
        <p class="card-text">Load your farm tractor with crops and deliver them safely across the fields.</p>
        <span class="card-plays">8K PLAYS</span>
      </div>
    </article>
  </div>

  <div class="bottom-menu">
    <svg class="menu-icon" viewBox="0 0 22 16"><rect width="22" height="3" fill="#1fb5d6"/><rect y="6.5" width="22" height="3" fill="#1fb5d6"/><rect y="13" width="22" height="3" fill="#1fb5d6"/></svg>
  </div>

  <footer class="site-footer"><span>© 2020 Vultaroo. All Rights Reserved.</span><span>Vultaroo.com</span></footer>
</div>
</body>
</html>
```